Harborline Renewal Business Card Design

Professional and clean design. The design colors should flow with the logo. Two-sided card with the website on the back which is:

www.HarborlineRenewal.example.

"Specializing in Water Damage Restoration"

On the front I need the name, email, phone, and logo.

Name: Darnell Quisby
Email: Darnell@HarborlineRenewal.example
Phone: 555-318-2046 for now

I only have the Preview and Thumbnail right now but should have the source files uploaded within a day or two.

Target Market(s)

Flood victims, home owners with water damage from busted pipes etc...

Industry/Entity Type

Business

Contact Information for Business Card

Name: Darnell Quisby

Font styles to use
Serif
Sans Serif

Requirements
Must have
• Business Card Details Info

```html
<!DOCTYPE html>
<html lang="en">
<head>
<meta charset="utf-8">
<title>Harborline Renewal Business Card</title>
<link href="https://fonts.googleapis.com/css2?family=Cinzel:wght@400;600&family=Open+Sans:wght@400;600&display=swap" rel="stylesheet">
<style>
  :root {
    --page-bg: #e9e9ea;
    --card-white: #ffffff;
    --card-dark: #3b3e41;
    --card-dark-edge: #2c2e31;
    --brand-light: #6cc3e6;
    --brand-blue: #2b8fd1;
    --text-dark: #3a3a3a;
    --text-mid: #555555;
  }
  * { box-sizing: border-box; margin: 0; padding: 0; }
  html, body {
    width: 1200px; height: 800px; overflow: hidden;
    background: var(--page-bg);
  }
  .sheet {
    position: relative; width: 1200px; height: 800px;
    display: flex; align-items: center; justify-content: center; gap: 40px;
  }
  .card {
    width: 540px; height: 310px; border-radius: 4px;
    box-shadow: 0 10px 28px rgba(0,0,0,0.18);
    position: relative; overflow: hidden;
  }

  /* Back side */
  .card-back {
    background: linear-gradient(160deg, var(--card-dark) 0%, var(--card-dark-edge) 100%);
    display: flex; flex-direction: column; align-items: center; justify-content: center;
    text-align: center; color: var(--brand-light);
  }
  .brand-mark {
    width: 58px; height: 58px; border-radius: 50%;
    background: var(--brand-light);
    margin-bottom: 16px;
  }
  .brand-name {
    font-family: "Cinzel", serif; font-weight: 600;
    color: var(--brand-light); letter-spacing: 2px; line-height: 1;
  }
  .card-back .brand-name { font-size: 34px; margin-bottom: 28px; }
  .tagline {
    font-family: "Open Sans", sans-serif; font-size: 14px;
    margin-bottom: 6px;
  }
  .website-back {
    font-family: "Open Sans", sans-serif; font-size: 14px;
  }

  /* Front side */
  .card-front {
    background: var(--card-white);
    display: flex; align-items: center;
  }
  .front-brand {
    width: 215px; height: 100%;
    display: flex; flex-direction: column; align-items: center; justify-content: center;
  }
  .front-brand .brand-mark { width: 92px; height: 92px; margin-bottom: 14px; }
  .front-brand .brand-name { font-size: 17px; letter-spacing: 1px; text-align: center; line-height: 1.3; }
  .divider {
    width: 1.5px; height: 190px; background: var(--brand-light);
  }
  .front-details {
    padding-left: 26px; flex: 1;
    font-family: "Open Sans", sans-serif; color: var(--text-dark);
  }
  .person-name {
    font-family: "Cinzel", serif; font-weight: 600; font-size: 22px;
    color: var(--brand-blue); letter-spacing: 1px;
  }
  .person-title {
    font-size: 11px; color: var(--text-mid); margin: 2px 0 14px;
  }
  .contact-list { list-style: none; }
  .contact-item {
    display: flex; align-items: center; gap: 8px;
    font-size: 13px; line-height: 1.65;
  }
  .contact-icon { width: 14px; height: 14px; flex-shrink: 0; }
  .address {
    margin-top: 12px; font-size: 12.5px; line-height: 1.55;
    color: var(--text-mid); text-transform: uppercase;
  }
</style>
</head>
<body>
<main class="sheet">
  <section class="card card-back" aria-label="Card back">
    <h2 class="brand-name">Harborline Renewal</h2>
    <div class="brand-mark" aria-hidden="true"></div>
    <p class="tagline">"Specializing in Water Damage Restoration"</p>
    <p class="website-back">www.HarborlineRenewal.example.</p>
  </section>

  <section class="card card-front" aria-label="Card front">
    <div class="front-brand">
      <div class="brand-mark" aria-hidden="true"></div>
      <h2 class="brand-name">Harborline<br>Renewal</h2>
    </div>
    <div class="divider" aria-hidden="true"></div>
    <div class="front-details">
      <h1 class="person-name">Darnell Quisby</h1>
      <p class="person-title">REALTOR</p>
      <ul class="contact-list">
        <li class="contact-item">
          <svg class="contact-icon" viewBox="0 0 16 16" aria-hidden="true">
            <circle cx="8" cy="8" r="8" fill="var(--brand-blue)"/>
            <path d="M5.2 4.2l1.4 0 .6 1.8-.9.7c.5 1 1.2 1.8 2.2 2.3l.7-.9 1.8.6v1.4c0 .4-.4.7-.8.7C7.1 10.6 4.6 8 4.5 4.9c0-.4.3-.7.7-.7z" fill="#fff"/>
          </svg>
          555-318-2046
        </li>
        <li class="contact-item">
          <svg class="contact-icon" viewBox="0 0 16 16" aria-hidden="true">
            <circle cx="8" cy="8" r="8" fill="var(--brand-blue)"/>
            <rect x="4" y="5.2" width="8" height="5.6" rx="0.6" fill="#fff"/>
            <path d="M4.3 5.5L8 8.4l3.7-2.9" stroke="var(--brand-blue)" stroke-width="0.9" fill="none"/>
          </svg>
          Darnell@HarborlineRenewal.example
        </li>
        <li class="contact-item">
          <svg class="contact-icon" viewBox="0 0 16 16" aria-hidden="true">
            <circle cx="8" cy="8" r="8" fill="var(--brand-blue)"/>
            <circle cx="8" cy="8" r="4.2" stroke="#fff" stroke-width="0.9" fill="none"/>
            <ellipse cx="8" cy="8" rx="1.8" ry="4.2" stroke="#fff" stroke-width="0.8" fill="none"/>
            <path d="M3.8 8h8.4" stroke="#fff" stroke-width="0.8"/>
          </svg>
          www.HarborlineRenewal.example
        </li>
      </ul>
      <p class="address">P.O. Box: 4417<br>Postal Code: 208, Coastal Province</p>
    </div>
  </section>
</main>
</body>
</html>
```